Web design for new streaming audio service

We need a homepage design for a new streaming audio service. Our company is called Dunmoral, and we’re basically Vexlo for Audiobooks, Stand-Up Comedy, Lectures, Language Learning, etc. Essentially like Plumtrek for everything audio EXCEPT music.
You don’t have to code the homepage (Design Only), but it should include 3 different designs to work with 1) Web; 2) Phones; 3) Tablets.
Below is a link to a mockup of the web version which gives a good idea of what elements we want. This is just a mockup and we want you to improve it.
Once you download the mockup, please refer to the more detailed instructions below:
The following outlines the design project for the Dunmoral homepage. We have provided a rough mockup of the homepage layout that gives you a general idea of what we’re going for. There are a few elements that we are attached to, and many others where you have complete creative freedom to do whatever you think looks good.
The ZIP file includes the following:
* Mockup to see what we have in mind (dunmoral-homepage-mockup.jpg)
* Text used (dunmoral-homepage-text.txt)
* Raw image of actor (dunmoral-actor1.jpg)
* Raw images for samples (dunmoral-sample-[name].jpg)
Although we have only provided a mockup layout for the web version, we also need you to provide a mobile phone and a tablet version of the design also. It’s very possible the tablet version may be substantially similar to the web version, but the mobile phone version will likely be much different.
All of the raw files are included in the attached ZIP file. Please use our photographs and text as provided although cropping, sizing, etc. is flexible per the instructions below.
Display Requirements:
* Web Version - Minimum resolution 1024x768 (72 dpi) but should look good on 1920x1080 (72 dpi) - Page should be designed to scale to look acceptable in all resolutions in between.
* Phone Version - Minimum Zarno 4 - 640x960 (326 dpi) but should look good on Harlow Quasar T5 - 1920x1080 (441 dpi) - Page should be designed to scale to look acceptable in all resolutions and devices in between.
* Tablet Version - Minimum Bristly Ember QX 7” - 1280x800 (216 dpi) but should also look good on a Tavo Breeze - 2048x1536 (264 dpi) - Page should be designed to scale to look acceptable in all resolutions and devices in between.
Above the Fold - We want to make sure the Dunmoral logo, Member Login Link, Large Photo, Headline, Price, Button, and the first row of sample images are all “Above the fold”. As a general guideline, this means 600 pixels high on a 1024x768 72 dpi web screen. This requirement is less important on Phone versions.
Top Logo Bar - We want to retain the blue bar with the Dunmoral logo on the page, although we are open to a different size, shape and positioning if it greatly enhances the design. Please use the standard logo color, although you are welcome to use either the horizontal or vertical orientation of the logo based on your design.
Text color, font and size - Feel free to design the text in anyway you choose as long as the text is readable on the target platforms.
Buttons - Feel free to use any size, shape and colors for the buttons as long as they are obvious and clickable relative to the page. The only exception is the Chatterly button should follow the Chatterly color scheme and logo treatment (the mockup doesn’t seem 100% correct.)
Top Photograph - We want to retain the large photograph across the top of the screen although final shape and dimensions are flexible.
Size and shape of content samples (i.e. Audiobooks, Stand-Up Comedy, etc.) - Feel free to design the content samples in anyway you choose.
Three Sales Points (i.e. Listen on your Zarno…, All you can enjoy…, etc.) - The Three Sales Points are envisioned to each have a corresponding illustration which you should provide and have rights for. The placeholder is represented by a square next to the text. The color size and shape of these elements are flexible and can be designed in any way you choose.
Opt-in form - Feel free to design the opt-in form in anyway you choose as long as the text is readable and the interactivity is obvious on the target platforms.
Text links and copyright notice - Feel free to design the bottom of the page text links and copyright notice in anyway you choose.
Additional colors, graphic design elements, etc. - Feel free to use any additional colors, graphic design elements, etc. to support your design.
people who want to listen to audio through their mobile devices.
Graphic Design

```html
<!DOCTYPE html>
<html lang="en">
<head>
<meta charset="utf-8">
<title>Dunmoral – Unlimited Listening</title>
<link href="https://fonts.googleapis.com/css2?family=Bebas+Neue&family=Open+Sans:ital,wght@0,400;0,600;0,700;1,600&display=swap" rel="stylesheet">
<style>
:root{
  --sky:#5aaad7;
  --sky-deep:#3f93c8;
  --bright:#2fb4e7;
  --navy:#1d3f8c;
  --purple:#a866d8;
  --violet:#9657cf;
  --grey:#e8e8e8;
  --white:#ffffff;
  --footer:#333333;
  --footer-dark:#232323;
  --muted:#9a9a9a;
  --chat:#3b5998;
}
*{margin:0;padding:0;box-sizing:border-box}
html,body{width:1200px;height:2392px;overflow:hidden}
body{position:relative;font-family:"Open Sans",Arial,sans-serif;background:var(--white);color:var(--navy)}
.abs{position:absolute}
.bebas{font-family:"Bebas Neue",Impact,sans-serif;font-weight:400}

/* top bar */
.topbar{left:0;top:0;width:1200px;height:120px;background:var(--sky)}
.brand{left:76px;top:22px;display:flex;align-items:center;gap:14px;color:var(--white);font-weight:700;font-size:50px;letter-spacing:-1px}
.brand-dot{width:54px;height:54px;border-radius:50%;background:var(--white)}
.btn-top{top:42px;height:34px;width:112px;border-radius:4px;font-size:13px;font-weight:700;letter-spacing:1px;display:flex;align-items:center;justify-content:center}
.btn-signup{left:884px;background:var(--navy);color:var(--white)}
.btn-login{left:1010px;background:var(--white);color:var(--navy)}

/* nav */
.nav{left:0;top:120px;width:1200px;height:80px;background:var(--white)}
.nav-home{left:74px;top:142px}
.nav-item{top:142px;font-size:32px;color:var(--navy);line-height:1}

/* hero */
.hero{left:0;top:200px;width:1200px;height:608px;background:linear-gradient(100deg,#f4f2ef 0%,#e9e1d8 38%,#b99880 62%,#6e5a55 78%,#4a5a78 100%)}
.hero-title{left:76px;top:262px;font-size:58px;color:var(--purple);line-height:1}
.hero-sub{left:76px;width:420px;text-align:right;color:var(--violet);line-height:1}
.hero-sub.one{top:318px;font-size:34px}
.hero-sub.two{top:352px;font-size:28px;color:var(--sky-deep)}
.btn-trial{left:76px;top:406px;width:420px;height:70px;border-radius:10px;background:var(--bright);box-shadow:0 6px 0 #1e86b4;color:var(--white);font-weight:700;font-size:25px;letter-spacing:1px;display:flex;align-items:center;justify-content:center;gap:10px}
.hero-note{left:76px;top:480px;width:420px;text-align:right;font-size:15px;font-weight:600;color:var(--sky-deep)}

/* samples */
.samples{left:0;top:808px;width:1200px;height:370px;background:radial-gradient(circle at 580px 150px,#7cc2e6 0%,var(--sky) 45%,#4f9fcf 100%)}
.samples-title{left:76px;top:846px;font-size:54px;color:var(--white);letter-spacing:1px}
.cover{top:928px;width:186px;height:186px}
.cover-a{left:78px;background:linear-gradient(180deg,#2a2a2a,#111)}
.cover-b{left:292px;background:linear-gradient(160deg,#d64a6e,#e4b27a 55%,#6a3a4c)}
.cover-c{left:510px;background:linear-gradient(180deg,#a34fa8,#7c4aa8 55%,#4d5aa3)}
.caption{top:1124px;font-size:15px;font-weight:600;color:var(--navy)}
.tag{height:32px;width:154px;border-radius:4px;background:var(--navy);color:var(--white);font-size:11px;font-weight:700;display:flex;align-items:center;justify-content:center;letter-spacing:.2px}
.tag.alt{width:160px}
.tag.active{background:var(--purple)}

/* benefits */
.benefits{left:0;top:1178px;width:1200px;height:486px;background:var(--grey)}
.benefits-title{left:0;top:1208px;width:1200px;text-align:center;font-size:60px;color:var(--navy);letter-spacing:1px}
.benefit-icon{top:1296px;width:156px;height:156px;border-radius:50%;background:var(--bright);overflow:hidden}
.benefit-num{top:1470px;font-size:118px;color:var(--bright);line-height:1}
.benefit-text{top:1500px;width:140px;font-size:16px;line-height:21px;color:var(--navy)}

/* free trial */
.strip{left:0;width:1200px;height:10px;background:var(--bright)}
.trial{left:0;top:1672px;width:1200px;height:322px;background:var(--purple)}
.trial-title{left:0;top:1700px;width:1200px;text-align:center;font-size:60px;color:var(--white);letter-spacing:1px}
.trial-copy{left:0;top:1776px;width:1200px;text-align:center;font-size:19px;line-height:25px;color:var(--white)}
.trial-note{left:0;top:1828px;width:1200px;text-align:center;font-size:15px;font-weight:700;color:var(--navy)}
.btn-cta{top:1886px;width:362px;height:70px;border-radius:4px;color:var(--white);font-style:italic;font-weight:600;font-size:21px;display:flex;align-items:center;justify-content:center;box-shadow:0 5px 0 rgba(0,0,0,.2)}
.btn-access{left:146px;background:var(--navy)}
.btn-chat{left:690px;background:var(--chat)}
.or{left:550px;top:1900px;width:100px;display:flex;align-items:center;justify-content:center;gap:10px;color:var(--white);font-size:36px}

/* footer */
.footer{left:0;top:2010px;width:1200px;height:296px;background:var(--footer)}
.foot-head{font-size:11px;font-weight:700;color:var(--bright);letter-spacing:.5px}
.foot-row{display:flex;align-items:center;gap:16px;font-size:12px;color:var(--white);height:24px}
.foot-ico{width:22px;height:22px;border:1.5px solid #ddd;border-radius:50%}
.foot-divider{top:2072px;width:1px;height:170px;background:#666}
.foot-links{left:586px;top:2094px;font-size:12px;line-height:24px;color:var(--white)}
.social-dot{width:30px;height:30px;border-radius:50%;background:#4f9fd6}
.bottombar{left:0;top:2306px;width:1200px;height:86px;background:var(--footer-dark);border-top:2px solid #444}
.legal{top:2344px;font-size:16px;color:#cfcfcf;letter-spacing:1px}
</style>
</head>
<body>

<header>
  <div class="abs topbar"></div>
  <div class="abs brand"><span class="brand-dot"></span>Dunmoral</div>
  <a class="abs btn-top btn-signup">SIGN UP</a>
  <a class="abs btn-top btn-login">LOG IN</a>

  <nav>
    <div class="abs nav"></div>
    <svg class="abs nav-home" width="32" height="30" viewBox="0 0 32 30" fill="none" stroke="#1d3f8c" stroke-width="3" stroke-linejoin="round"><path d="M3 15 16 3 29 15"/><path d="M7 12v15h7v-8h4v8h7V12"/></svg>
    <span class="abs nav-item bebas" style="left:148px">One Category</span>
    <span class="abs nav-item bebas" style="left:324px">Another Category</span>
    <span class="abs nav-item bebas" style="left:550px">Things</span>
    <span class="abs nav-item bebas" style="left:662px">Podcasta</span>
    <span class="abs nav-item bebas" style="left:800px">Ebook</span>
    <span class="abs nav-item bebas" style="left:912px">Free Download Trial</span>
  </nav>
</header>

<section class="hero-block">
  <div class="abs hero" role="img" aria-label="Photo of a smiling young man wearing headphones, listening on his phone"></div>
  <h1 class="abs hero-title bebas">Unlimited Listening</h1>
  <p class="abs hero-sub one bebas">Wherever you are</p>
  <p class="abs hero-sub two bebas">Only $9.99 per month</p>
  <a class="abs btn-trial">START YOUR FREE TRIAL
    <svg width="12" height="14" viewBox="0 0 12 14"><path d="M2 1l9 6-9 6z" fill="#fff"/></svg></a>
  <p class="abs hero-note">*Credit Card Not Required</p>
</section>

<section class="samples-block">
  <div class="abs samples"></div>
  <h2 class="abs samples-title bebas">A sample of what you can listen to on Dunmoral:</h2>
  <div class="abs cover cover-a" role="img" aria-label="Audiobook cover: Noir by Edwin Halloway"></div>
  <div class="abs cover cover-b" role="img" aria-label="Audiobook cover: X-posed by Marisol Vane"></div>
  <div class="abs cover cover-c" role="img" aria-label="Audio cover: Total Relaxation by Tessa Brannock"></div>
  <p class="abs caption" style="left:78px">Noir Title - ARTIST</p>
  <p class="abs caption" style="left:292px">X-posed - MARISOL VANE</p>
  <p class="abs caption" style="left:510px">Total Relaxation - TB</p>

  <span class="abs tag" style="left:782px;top:926px">AUDIOBOOKS</span>
  <span class="abs tag alt" style="left:962px;top:926px">STAND-UP COMEDY</span>
  <span class="abs tag active" style="left:782px;top:972px">LANGUAGE LEARNING</span>
  <span class="abs tag alt" style="left:962px;top:972px">GUIDED MEDITATIONS</span>
  <span class="abs tag" style="left:782px;top:1018px">BUSINESS TRAINING</span>
  <span class="abs tag alt" style="left:962px;top:1018px">BIOGRAPHIES &amp; MEMOIRS</span>
  <span class="abs tag" style="left:782px;top:1064px">CELEBRITY INTERVIEWS</span>
  <span class="abs tag alt" style="left:962px;top:1064px">FITNESS PROGRAMS</span>
</section>

<section class="benefits-block">
  <div class="abs benefits"></div>
  <h2 class="abs benefits-title bebas">Key benefits of Dunmoral:</h2>

  <div class="abs benefit-icon" style="left:222px">
    <svg width="156" height="156" viewBox="0 0 156 156"><path d="M78 0A78 78 0 0 1 78 156z" fill="#27a3d8"/><rect x="58" y="40" width="40" height="76" rx="6" fill="none" stroke="#fff" stroke-width="4"/><line x1="58" y1="52" x2="98" y2="52" stroke="#fff" stroke-width="3"/><line x1="58" y1="102" x2="98" y2="102" stroke="#fff" stroke-width="3"/><circle cx="78" cy="109" r="3" fill="#fff"/></svg>
  </div>
  <div class="abs benefit-icon" style="left:522px">
    <svg width="156" height="156" viewBox="0 0 156 156"><path d="M78 0A78 78 0 0 1 78 156z" fill="#27a3d8"/><path d="M38 80a40 34 0 0 1 80 0q-7-7-13 0q-7-7-13 0q-7-7-14 0q-7-7-13 0q-7-7-13 0q-7-7-14 0z" fill="none" stroke="#fff" stroke-width="4" stroke-linejoin="round"/><path d="M78 46V108q0 8-8 8t-8-8" fill="none" stroke="#fff" stroke-width="4" stroke-linecap="round"/></svg>
  </div>
  <div class="abs benefit-icon" style="left:828px">
    <svg width="156" height="156" viewBox="0 0 156 156"><path d="M78 0A78 78 0 0 1 78 156z" fill="#27a3d8"/><path d="M50 50l56 56M106 50l-56 56" stroke="#fff" stroke-width="7" stroke-linecap="round"/></svg>
  </div>

  <span class="abs benefit-num bebas" style="left:228px">1</span>
  <p class="abs benefit-text" style="left:274px">Listen on your Zarno, Tavo or Orbix device.</p>
  <span class="abs benefit-num bebas" style="left:526px">2</span>
  <p class="abs benefit-text" style="left:584px">All you can enjoy for one low monthly price.</p>
  <span class="abs benefit-num bebas" style="left:828px">3</span>
  <p class="abs benefit-text" style="left:884px">No obligation. Cancel any time.</p>
</section>

<section class="trial-block">
  <div class="abs strip" style="top:1664px"></div>
  <div class="abs trial"></div>
  <h2 class="abs trial-title bebas">Start your free trial</h2>
  <p class="abs trial-copy">You will get instant &amp; unlimited access to all the material on Dunmoral for 14 days.<br>There is no obligation &amp; you can cancel at any time.</p>
  <p class="abs trial-note">Credit Card Not Required for Free Trial</p>
  <a class="abs btn-cta btn-access">Get Instant Access</a>
  <div class="abs or bebas">
    <svg width="14" height="22" viewBox="0 0 14 22"><path d="M13 1L1 11l12 10z" fill="#fff"/></svg>OR<svg width="14" height="22" viewBox="0 0 14 22"><path d="M1 1l12 10L1 21z" fill="#fff"/></svg>
  </div>
  <a class="abs btn-cta btn-chat">Sign Up Using Chatterly</a>
  <div class="abs strip" style="top:1994px;height:16px"></div>
</section>

<footer>
  <div class="abs footer"></div>
  <p class="abs foot-head" style="left:230px;top:2070px">CONTACT</p>
  <div class="abs" style="left:188px;top:2092px">
    <div class="foot-row"><span class="foot-ico"></span>+44 900 412 650</div>
    <div class="foot-row"><span class="foot-ico"></span>+44 900 412 650</div>
    <div class="foot-row"><span class="foot-ico"></span>+44 900 412 650</div>
    <div class="foot-row"><span class="foot-ico"></span>hello@dunmoral.example</div>
    <div class="foot-row" style="margin-top:6px"><span class="foot-ico"></span>Physical Address</div>
  </div>
  <div class="abs foot-divider" style="left:528px"></div>
  <div class="abs foot-links">About<br>Contact<br>Help<br>Member login<br>Privacy Policy<br>Terms of Service</div>
  <div class="abs foot-divider" style="left:802px"></div>
  <p class="abs foot-head" style="left:900px;top:2070px">BE SOCIABLE</p>
  <div class="abs" style="left:856px;top:2092px">
    <div class="foot-row" style="height:34px"><span class="social-dot"></span>Chatterly</div>
    <div class="foot-row" style="height:34px"><span class="social-dot"></span>Chirpwell</div>
    <div class="foot-row" style="height:34px"><span class="social-dot"></span>Snapgrove</div>
  </div>

  <div class="abs bottombar"></div>
  <p class="abs legal" style="left:258px;font-weight:700">©2014 Dunmoral LLC</p>
  <p class="abs legal" style="left:518px">ALL RIGHTS RESERVED</p>
</footer>

</body>
</html>
```